Clear Plastic Card Design

I am looking to have a business card designed from my logo icon. I am looking to match the style of a different business card I have attached in the files.
Looking for a card that is plastic, with layers of transparency in the shape of my logo icon (also attached in the files) - not a circle like the other card. The winning design will incorporate the red icon logo on the front and back and include the charity's name, "Light for the Weary Souls" in the same or similar font, as well as an email and phone number. For now, use the email: email@lightfortheweary-mail.org and the phone number 555-382-7194.
We like how the sample business card has transparency, partial and full opacity layers and a matching color scheme. Files will need to be in vector so that our business card printing company can work with it.
UPDATE:
We've some excellent designs in, thank you everyone! I got an early review from the owner, and he requested a minor redirect to find his perfect design. He wants the design to stand out by NOT being a rectangle. Try instead a circle, square, or best yet - something that falls in the outline of the logo icon, either fully or partially. Thank you, everyone!
Light for the Weary Souls text should be incorporated as well as a phone and email.

```html
<!DOCTYPE html>
<html lang="en">
<head>
<meta charset="utf-8">
<title>Light for the Weary Souls – Clear Plastic Business Card</title>
<link href="https://fonts.googleapis.com/css2?family=Poppins:wght@400;500;600&display=swap" rel="stylesheet">
<style>
  :root{
    --bg:#d3c6b6;
    --bg-light:#e2d8cc;
    --frost:rgba(250,244,236,0.55);
    --frost-edge:rgba(255,255,255,0.85);
    --red:rgba(196,20,28,0.92);
    --red-clear:rgba(178,12,20,0.82);
    --red-layer:rgba(140,6,14,0.35);
    --orange:#e26a1f;
    --ink:#1d1a18;
    --cream:#f5e8de;
  }
  *{margin:0;padding:0;box-sizing:border-box}
  html,body{width:1200px;height:539px;overflow:hidden}
  body{
    background:radial-gradient(ellipse at 50% 40%,var(--bg-light) 0%,var(--bg) 75%);
    font-family:'Poppins',sans-serif;position:relative;
  }
  .card{position:absolute;width:486px;height:265px}
  .card-front{left:79px;top:150px}
  .card-back{left:660px;top:151px}
  .card-shape{position:absolute;left:0;top:0}
  .brand-name{position:absolute;left:0;right:0;top:26px;text-align:center;color:var(--red);font-weight:600;font-size:20px;line-height:1.2}
  .person{position:absolute;left:0;right:0;top:106px;text-align:center;font-size:19px;line-height:1;color:#c3161e;font-weight:600}
  .person .surname{color:var(--orange);font-weight:400}
  .role{position:absolute;left:0;right:0;top:131px;text-align:center;font-size:10.5px;line-height:1;font-weight:500;color:var(--ink)}
  .icons{position:absolute;left:0;right:0;top:148px;display:flex;justify-content:center;gap:6px}
  .contact{position:absolute;left:0;right:0;text-align:center;font-size:12.2px;line-height:1;color:var(--ink);letter-spacing:.3px}
  .phone{top:168px}
  .web{top:183px}
  .email{top:198px}
  .address{position:absolute;left:0;right:0;top:237px;text-align:center;font-size:11px;line-height:1;color:var(--cream);letter-spacing:.4px}
  .back-name{position:absolute;left:0;right:0;top:100px;text-align:center;color:var(--cream);font-weight:400;font-size:28px;line-height:1.15}
</style>
</head>
<body>
  <section class="card card-front">
    <svg class="card-shape" width="486" height="265" viewBox="0 0 486 265">
      <defs>
        <clipPath id="front-outline">
          <path d="M18 0 H430 L486 56 V247 Q486 265 468 265 H18 Q0 265 0 247 V18 Q0 0 18 0 Z"/>
        </clipPath>
      </defs>
      <g clip-path="url(#front-outline)">
        <rect width="486" height="265" fill="var(--frost)"/>
        <path d="M0 188 Q243 266 486 183 L486 265 L0 265 Z" fill="var(--red)"/>
        <path d="M0 230 Q200 200 486 245 L486 265 L0 265 Z" fill="var(--red-layer)"/>
        <path d="M18 186 Q243 262 470 180" fill="none" stroke="var(--orange)" stroke-width="3"/>
      </g>
      <path d="M18 0.5 H430 L485.5 56 V247 Q485.5 264.5 468 264.5 H18 Q0.5 264.5 0.5 247 V18 Q0.5 0.5 18 0.5 Z" fill="none" stroke="var(--frost-edge)" stroke-width="1.2"/>
    </svg>
    <div class="brand-name">Light for the<br>Weary Souls</div>
    <div class="person">Marta <span class="surname">Kovalenko</span></div>
    <div class="role">Founder &amp; CEO</div>
    <div class="icons">
      <svg width="18" height="18" viewBox="0 0 18 18" aria-label="phone"><rect x="3.5" y="3.5" width="11" height="11" transform="rotate(45 9 9)" fill="none" stroke="#c3161e" stroke-width="1.5"/><path d="M6.5 6.5 Q7 10.5 11.5 11.5 L11.5 10 L10 9.5 L9.3 10.2 Q8 9.5 7.8 8.2 L8.5 7.5 L8 6 Z" fill="#c3161e"/></svg>
      <svg width="18" height="18" viewBox="0 0 18 18" aria-label="email"><rect x="3.5" y="3.5" width="11" height="11" transform="rotate(45 9 9)" fill="none" stroke="#c3161e" stroke-width="1.5"/><rect x="6" y="7" width="6" height="4.5" fill="none" stroke="#c3161e" stroke-width="1"/><path d="M6 7 L9 9.5 L12 7" fill="none" stroke="#c3161e" stroke-width="1"/></svg>
      <svg width="18" height="18" viewBox="0 0 18 18" aria-label="website"><rect x="3.5" y="3.5" width="11" height="11" transform="rotate(45 9 9)" fill="none" stroke="#c3161e" stroke-width="1.5"/><circle cx="9" cy="9" r="3" fill="none" stroke="#c3161e" stroke-width="1"/><path d="M6 9 H12 M9 6 Q7.5 9 9 12 Q10.5 9 9 6" fill="none" stroke="#c3161e" stroke-width=".8"/></svg>
    </div>
    <div class="contact phone">555-382-7194.</div>
    <div class="contact web">www.lightfortheweary-souls.org</div>
    <div class="contact email">email@lightfortheweary-mail.org</div>
    <div class="address">1840 Meadowbrook Ln. Suite 310 Denton, TX 76201</div>
  </section>

  <section class="card card-back">
    <svg class="card-shape" width="486" height="265" viewBox="0 0 486 265">
      <defs>
        <clipPath id="back-outline">
          <path d="M56 0 H468 Q486 0 486 18 V247 Q486 265 468 265 H18 Q0 265 0 247 V56 Z"/>
        </clipPath>
      </defs>
      <g clip-path="url(#back-outline)">
        <rect width="486" height="265" fill="var(--red-clear)"/>
        <path d="M0 120 Q150 60 260 140 T486 110 V265 H0 Z" fill="var(--red-layer)"/>
      </g>
      <path d="M56 0.5 H468 Q485.5 0.5 485.5 18 V247 Q485.5 264.5 468 264.5 H18 Q0.5 264.5 0.5 247 V56 Z" fill="none" stroke="rgba(255,255,255,0.45)" stroke-width="1.2"/>
    </svg>
    <div class="back-name">Light for the<br>Weary Souls</div>
  </section>
</body>
</html>
```